Meridian Crestline Motors *

Professional business cards for our auto wholesale dealership.

Target Market(s)

New and used cars sales managers and middle class to higher end private party buyers.

Industry/Entity Type

Automotive

Contact Information for Business Card

Meridian Crestline Motors
Darnell R Okonski
Owner
(555) 304-6618
mercrestmotors@quillbox.example
Dealer Lic # 48265

Logo Text

Meridian Crestline Motors, Mer Crest Motors, MCM, etc

Font styles to use
Serif
Sans Serif

Colors

Designer to choose colors to be used in the design.

Requirements
Must have
• A professional, but not pretentious, look
Nice to have
• It might be nice to see "MCM" in a shape form i.e. circle, triangle, etc in the corner or background somehwere
Should not have
• bright "girly" colors

```html
<!DOCTYPE html>
<html lang="en">
<head>
<meta charset="utf-8">
<title>Meridian Crestline Motors — Business Card</title>
<link rel="stylesheet" href="https://fonts.googleapis.com/css2?family=Source+Sans+3:wght@400&family=Figtree:wght@400&family=Roboto+Condensed:wght@400&display=swap">
<style>
  :root {
    --brand-teal: #04677a;
    --ink: #1c1c1c;
    --card: #ffffff;
    --backdrop: #c4c4c4;
  }
  * { margin: 0; padding: 0; box-sizing: border-box; }
  html, body { width: 1200px; height: 1200px; overflow: hidden; }
  body { background: var(--backdrop); position: relative; font-family: "Figtree", sans-serif; }

  .card {
    position: absolute;
    left: 308px;
    width: 627px;
    height: 356px;
    background: var(--card);
    border-radius: 34px;
    overflow: hidden;
  }
  .card--front { top: 188px; }
  .card--back { top: 653px; }

  .holder {
    position: absolute;
    left: 45px;
    top: 54px;
    display: flex;
    align-items: center;
    white-space: nowrap;
  }
  .holder__name {
    font-family: "Source Sans 3", sans-serif;
    font-size: 25px;
    color: var(--brand-teal);
  }
  .holder__divider {
    width: 1.5px;
    height: 22px;
    background: var(--brand-teal);
    margin: 0 14px 0 15px;
  }
  .holder__role { font-size: 16px; color: var(--ink); padding-top: 4px; }

  .front-disc {
    position: absolute;
    left: -5px;
    top: 176px;
    width: 270px;
    height: 270px;
  }
  .front-monogram {
    position: absolute;
    z-index: 1;
    left: 45px;
    top: 122px;
    font-family: "Roboto Condensed", sans-serif;
    font-size: 34px;
    line-height: 1;
    letter-spacing: 1px;
    color: var(--brand-teal);
  }

  .contact {
    position: absolute;
    left: 318px;
    top: 218px;
    font-size: 16px;
    color: var(--ink);
    list-style: none;
    white-space: nowrap;
  }
  .contact__item { display: flex; align-items: center; height: 25px; }
  .contact__icon { width: 17px; height: 17px; margin-right: 6px; flex: none; }
  .contact__license { margin-top: 21px; }

  .back-disc {
    position: absolute;
    left: 223px;
    top: 58px;
    width: 180px;
    height: 180px;
  }
  .back-name {
    position: absolute;
    left: 0;
    right: 0;
    top: 258px;
    text-align: center;
    font-family: "Roboto Condensed", sans-serif;
    font-size: 31px;
    color: var(--brand-teal);
  }
</style>
</head>
<body>

<section class="card card--front">
  <div class="holder">
    <span class="holder__name">Darnell R Okonski</span>
    <span class="holder__divider"></span>
    <span class="holder__role">Owner</span>
  </div>

  <svg class="front-disc" viewBox="0 0 270 270" aria-hidden="true">
    <circle cx="135" cy="135" r="135" fill="var(--brand-teal)"/>
  </svg>
  <span class="front-monogram">MCM</span>

  <ul class="contact">
    <li class="contact__item">
      <svg class="contact__icon" viewBox="0 0 24 24" aria-hidden="true">
        <path fill="var(--brand-teal)" d="M6.6 10.8a15.5 15.5 0 0 0 6.6 6.6l2.2-2.2a1 1 0 0 1 1-.25 11.4 11.4 0 0 0 3.6.57 1 1 0 0 1 1 1V20a1 1 0 0 1-1 1A17 17 0 0 1 3 4a1 1 0 0 1 1-1h3.5a1 1 0 0 1 1 1c0 1.25.2 2.45.57 3.57a1 1 0 0 1-.25 1z"/>
      </svg>
      (555) 304-6618
    </li>
    <li class="contact__item">
      <svg class="contact__icon" viewBox="0 0 24 24" aria-hidden="true">
        <rect x="2" y="7" width="20" height="14" rx="1.5" fill="var(--brand-teal)"/>
        <path d="M3 8l9 7 9-7" fill="none" stroke="#fff" stroke-width="1.6"/>
      </svg>
      mercrestmotors@quillbox.example
    </li>
    <li class="contact__item contact__license">Dealer Lic # 48265</li>
  </ul>
</section>

<section class="card card--back">
  <svg class="back-disc" viewBox="0 0 180 180" aria-hidden="true">
    <circle cx="90" cy="90" r="90" fill="var(--brand-teal)"/>
  </svg>
  <p class="back-name">Meridian Crestline Motors</p>
</section>

</body>
</html>
```